Business card design for a dynamic IT consulting company

We need a business card design for a young firm, specialized in the Telecommunications/Consulting industry. The name of the company is Quindor and Partners Business Consulting Ltd. (Short name: Quindor and Partnes)
Quindor = solve read reverse, so we aim to be uncomplicated and solution-oriented. The small pipe in our logo is also related to the word solve. So we need a new business card design, which is simple, eye catching and something non traditional (I would probably prefer a square shaped design rather than a rectangle, but open for suggestions). Attached our logo.

Target Market(s)

Usually our customers are Tier1 Telecoms providers (Q-Netra, Palorix, etc) and their executives.

Industry/Entity Type

Business

Contact Information for Business Card

Name: Bence Tolnavari
Email: b.tolnavari@quindor.hu
Web: www.quindor.hu
Mobile: +36 30 518 2769
Title: Managing Director

Optional:
Company name: Quindor and Partners Ltd.
Address: 1087 Budapest, Tolvenka str. 28/C, Hungary

Font styles to use
Other font styles liked:
• helveticaneue_medium, Prime Regular are used now.

Colors

Designer to choose colors to be used in the design.

Requirements
Must have
• I would like to have a 2 sided design.
Nice to have
• I thought if we make the logo a bit bigger (without the company name), that could go to the back with the company name below. I though, if the pipe in the logo is somehow touchable on the business card, would be nice and unique.

```html
<!DOCTYPE html>
<html lang="en">
<head>
<meta charset="utf-8">
<title>Quindor &amp; Partners – Business Card</title>
<link href="https://fonts.googleapis.com/css2?family=Arimo:wght@400;700&display=swap" rel="stylesheet">
<style>
  :root {
    --backdrop: #2b2b2c;
    --card-front: #f1f1f1;
    --card-back: #5b5c5e;
    --accent-blue: #0a97d4;
    --accent-pink: #b8399a;
    --text-grey: #555659;
    --white: #ffffff;
  }
  * { margin: 0; padding: 0; box-sizing: border-box; }
  html, body {
    width: 1200px; height: 960px; overflow: hidden;
    background: var(--backdrop);
    font-family: "Arimo", "Helvetica Neue", Arial, sans-serif;
  }
  .stage { position: relative; width: 1200px; height: 960px; }
  .card {
    position: absolute; top: 305px;
    width: 344px; height: 343px;
    border-bottom: 11px solid var(--accent-blue);
    box-shadow: 0 2px 6px rgba(0,0,0,.45);
  }
  .card--front { left: 200px; background: var(--card-front); }
  .card--back { left: 651px; background: var(--card-back); }

  .brand {
    position: absolute; top: 34px; left: 0; right: 0;
    display: flex; align-items: center; justify-content: center; gap: 10px;
  }
  .brand__mark { width: 14px; height: 14px; background: var(--accent-pink); }
  .brand__name {
    font-size: 25px; font-weight: 400; color: var(--text-grey);
    letter-spacing: 0.2px;
  }

  .contact {
    position: absolute; top: 176px; left: 0; right: 0;
    text-align: center; color: var(--text-grey);
    font-variant: small-caps;
  }
  .contact__name {
    font-size: 19px; font-weight: 700; color: var(--accent-blue);
    line-height: 22px;
  }
  .contact__title { font-size: 16px; line-height: 20px; }
  .contact__details { margin-top: 12px; font-size: 15px; line-height: 18px; }

  .back-brand {
    position: absolute; top: 0; left: 0; right: 0; bottom: 0;
    display: flex; align-items: center; justify-content: center; gap: 14px;
  }
  .back-brand__mark { width: 18px; height: 18px; background: var(--accent-blue); }
  .back-brand__name { font-size: 34px; font-weight: 400; color: var(--white); }
</style>
</head>
<body>
  <main class="stage">
    <section class="card card--front" aria-label="Card front">
      <div class="brand">
        <span class="brand__mark"></span>
        <span class="brand__name">Quindor &amp; Partners</span>
      </div>
      <div class="contact">
        <p class="contact__name">Bence Tolnavari</p>
        <p class="contact__title">Managing Director</p>
        <div class="contact__details">
          <p>Quindor and Partners Ltd.</p>
          <p>1087 Budapest</p>
          <p>Tolvenka str. 28/C, Hungary</p>
          <p>+36 30 518 2769</p>
        </div>
      </div>
    </section>

    <section class="card card--back" aria-label="Card back">
      <div class="back-brand">
        <span class="back-brand__mark"></span>
        <span class="back-brand__name">Quindor</span>
      </div>
    </section>
  </main>
</body>
</html>
```